Harborview Grace Chapel: Steadfast Conference

We need a flyer, powerpoint, and possible email template for our Church's Bible Conference for October 6th-8th. The conference is called Steadfast (Standing Courageously in Truth).

The purpose of the conference is that we would like to encourage believers to stand courageously on the absolute authority of God’s word, to know the truth and to stand courageously for it.

This is the Conference information below

Sunday: 9:30AM: Pastor Tomasz Belvadine: Delivered from Fear
11am: Dr. Howard Pellin: Standing for Righteousness in a politically correct society

7pm: Dr. Raymond Tisdale: Courageously facing Immortality

Monday: Dr. Howard Pellin: The Stand for Righteousness as a Christian Educator

Tuesday: Pastor Tomasz Belvadine: Courageously Proclaiming Christ in Muslim Territory

Wednesday: Dr. Raymond Tisdale: Stand for Righteousness in the Last Days

An idea that we had could be 3 or 4 people facing a large crowd, illuminated with the bible as their guide. I don't know how hard that would be to design, but basically something that emphasizes Steadfast in regards to the bible.

If you have any questions please message me at anytime, a team of 3 of us will be selecting the top design.
Updates

Project Deadline Extended
Reason: Some of our team members who are selecting had to travel abroad and won't be back in the office till monday. We also would like to see more designs as well.

Target Market(s)

All Ages

Industry/Entity Type

Church

Requirements
Must have
• Email
Flyer
Powerpoint describing Flyer: Could be two or 3 slides
Harborview Grace Chapel
2013 Bible Conference

```html
<!DOCTYPE html>
<html lang="en">
<head>
<meta charset="utf-8">
<title>Steadfast – Harborview Grace Chapel 2013 Bible Conference</title>
<link rel="stylesheet" href="https://fonts.googleapis.com/css2?family=Cinzel:wght@400;600;700&family=Arimo:ital,wght@0,400;0,700;1,400&display=swap">
<style>
  :root {
    --ink: #0b0b0b;
    --white: #ffffff;
    --silver: #e6e6e6;
    --gold-light: #f7ecc8;
    --gold-mid: #e3cf93;
    --gold-deep: #b99a55;
    --crowd-dark: #3a2a22;
    --crowd-warm: #8a5a3c;
    --crowd-light: #c99b78;
    --divider: rgba(120, 95, 45, 0.35);
  }
  * { box-sizing: border-box; margin: 0; padding: 0; }
  html, body { width: 1200px; height: 1068px; overflow: hidden; background: var(--ink); }
  .flyer {
    position: relative; width: 1200px; height: 1068px; overflow: hidden;
    font-family: "Arimo", Arial, sans-serif; color: var(--ink);
  }
  .hero-photo {
    position: absolute; left: 0; top: 0; width: 1200px; height: 556px;
    background:
      radial-gradient(ellipse at 20% 40%, rgba(255,240,220,0.35), transparent 45%),
      radial-gradient(ellipse at 70% 20%, var(--crowd-light), transparent 60%),
      linear-gradient(180deg, var(--crowd-warm) 0%, var(--crowd-dark) 100%);
  }
  .title-block {
    position: absolute; left: 520px; top: 150px; width: 620px; text-align: center;
    color: var(--white);
  }
  .title {
    font-family: "Cinzel", "Times New Roman", serif; font-weight: 600;
    font-size: 96px; line-height: 1; letter-spacing: 1px;
    background: linear-gradient(180deg, #ffffff 0%, #f2f2f2 55%, #bdbdbd 100%);
    -webkit-background-clip: text; background-clip: text; color: transparent;
    text-shadow: 0 3px 8px rgba(0,0,0,0.25);
  }
  .subtitle {
    font-family: "Cinzel", "Times New Roman", serif; font-weight: 600;
    font-size: 27px; margin-top: 4px; letter-spacing: 0.3px;
  }
  .rule { display: block; margin: 6px auto 0; width: 580px; height: 3px; background: var(--silver); }
  .date {
    font-family: "Cinzel", "Times New Roman", serif; font-weight: 600;
    font-size: 40px; margin-top: 44px;
  }
  .schedule {
    position: absolute; left: 0; top: 556px; width: 1200px; height: 456px;
    background: linear-gradient(100deg, var(--gold-mid) 0%, var(--gold-light) 30%, var(--gold-deep) 55%, var(--gold-light) 80%, var(--gold-mid) 100%);
    display: flex;
  }
  .day {
    position: relative; flex: 1; text-align: center; padding-top: 0;
    border-right: 2px solid var(--divider);
  }
  .day:last-child { border-right: none; }
  .day-tab {
    display: inline-block; margin-top: 0; padding: 8px 14px 6px;
    background: var(--ink); color: var(--white);
    font-family: "Cinzel", "Times New Roman", serif; font-weight: 600;
    font-size: 48px; line-height: 1.2;
  }
  .sessions { margin-top: 18px; font-size: 21px; line-height: 1.2; }
  .session { margin-bottom: 28px; }
  .speaker { font-style: italic; }
  .start { font-size: 23px; margin-top: 34px; }
  .talk-speaker { font-size: 23px; font-style: italic; margin-top: 38px; }
  .talk-title { font-size: 24px; line-height: 1.22; margin-top: 40px; }
  .footer {
    position: absolute; left: 0; top: 1012px; width: 1200px; height: 56px;
    background: var(--ink); color: var(--white); text-align: center;
    font-family: "Cinzel", "Times New Roman", serif; font-weight: 600;
    font-size: 28px; line-height: 56px; letter-spacing: 1px;
  }
</style>
</head>
<body>
<main class="flyer">
  <div class="hero-photo" role="img" aria-label="A preacher seen from behind at a wooden pulpit, facing a large cheering crowd with raised hands"></div>

  <header class="title-block">
    <h1 class="title">STEADFAST</h1>
    <p class="subtitle">Standing Courageously in Truth</p>
    <span class="rule"></span>
    <p class="date">October 6th–9th</p>
  </header>

  <section class="schedule">
    <article class="day">
      <h2 class="day-tab">Sunday</h2>
      <div class="sessions">
        <p class="session">9:30 am<br><span class="speaker">Pastor Tomasz Belvadine</span>:<br>Delivered from Fear</p>
        <p class="session">11:00 am<br><span class="speaker">Dr. Howard Pellin:</span><br>Standing for Righteousness<br>in a Politically<br>incorrect Society</p>
        <p class="session">7:00 pm<br><span class="speaker">Dr. Raymond Tisdale:</span><br>Courageously Facing<br>My Mortality</p>
      </div>
    </article>
    <article class="day">
      <h2 class="day-tab">Monday</h2>
      <p class="start">Start Time: 7:30pm</p>
      <p class="talk-speaker">Dr. Howard Pellin:</p>
      <p class="talk-title">Standing for<br>Righteousness as a<br>Christian Educator</p>
    </article>
    <article class="day">
      <h2 class="day-tab">Tuesday</h2>
      <p class="start">Start Time: 7:30pm</p>
      <p class="talk-speaker">Pastor Tomasz<br>Belvadine:</p>
      <p class="talk-title" style="margin-top:28px">Courageously<br>Proclaiming Christ<br>in Muslim Territories</p>
    </article>
    <article class="day">
      <h2 class="day-tab">Wednesday</h2>
      <p class="start">Start Time: 7:30pm</p>
      <p class="talk-speaker">Dr. Raymond Tisdale:</p>
      <p class="talk-title">Stand for<br>Righteousness<br>in the Last Days</p>
    </article>
  </section>

  <footer class="footer">Harborview Grace Chapel 2013 Bible Conference</footer>
</main>
</body>
</html>
```